Signage Design Project

We need a logo and signage for the shopfront of a personal fitness training gym and coaching facility. We want the signage to cover the glass shopfront windows which consist of 4 glass windows with dimensions: 1 of 200cm x 180cm, 2 of 180cm x 135cm and 1 of 180cm x 180cm. The windows that are 200x 180 and 180x180 are the most visable/ important. We want the 200x180 to display the logo and our name which is "Ridgeline Fitness Centre" with further information of: Your personal training studio and boutique coaching gym Ph: 9471 2836.
For the window with 180 x 180cm measurement we want to list the services we provide which are:
Personal Training Sessions | Group Classes|Weight Loss |Toning & Sculpting|Bodybuilding I Cardio|Weights| Kettlebells| Boxing| Circuits I Team Building Programs| Boot Camp I Healthy Lifestyle & Wellness Coaching
The 2 windows 180x135cm are diagonal to the entry of the shop. We want them to be the same and plainer in design with the words: Ridgeline Fitness Centre
Personal Training Studio and Boutique Coaching Gym
The signage design also includes an acrylic window box that lights up which is to display the logo and Ridgeline Fitness Centre

```html
<!DOCTYPE html>
<html lang="en">
<head>
<meta charset="utf-8">
<title>Ridgeline Fitness Centre – Window Sign</title>
<link rel="stylesheet" href="https://fonts.googleapis.com/css2?family=Questrial&display=swap">
<style>
  :root {
    --page: #ffffff;
    --leaf-green: #a8b526;
    --blue-light: #00b8ee;
    --blue-mid: #0093bf;
    --blue-deep: #006c88;
    --ink: #ffffff;
  }
  * { margin: 0; padding: 0; box-sizing: border-box; }
  html, body {
    width: 1200px;
    height: 900px;
    overflow: hidden;
    background: var(--page);
  }
  .sign {
    position: relative;
    width: 1200px;
    height: 900px;
    font-family: "Questrial", "Century Gothic", sans-serif;
    color: var(--ink);
  }
  .sign-panel {
    position: absolute;
    left: 163px;
    top: 53px;
    width: 884px;
    height: 793px;
  }
  .brand {
    position: absolute;
    left: 225px;
    top: 212px;
    width: 770px;
    display: flex;
    align-items: center;
    gap: 22px;
  }
  .brand-mark {
    width: 34px;
    height: 34px;
    background: var(--ink);
    flex: none;
  }
  .brand-name {
    font-weight: 400;
    line-height: 1;
    text-transform: uppercase;
  }
  .brand-name .line-main {
    display: block;
    font-size: 104px;
    letter-spacing: 4px;
  }
  .brand-name .line-sub {
    display: block;
    font-size: 50px;
    letter-spacing: 5px;
    text-align: right;
    margin-top: 10px;
  }
  .tagline {
    position: absolute;
    left: 163px;
    width: 884px;
    top: 463px;
    text-align: center;
    font-size: 40px;
    line-height: 44px;
    letter-spacing: 4px;
    word-spacing: 6px;
  }
  .contact {
    position: absolute;
    left: 163px;
    width: 884px;
    top: 668px;
    display: flex;
    justify-content: center;
    align-items: center;
    gap: 14px;
    font-size: 74px;
    letter-spacing: 2px;
    line-height: 1;
  }
  .contact-icon { width: 36px; height: 58px; flex: none; }
</style>
</head>
<body>
<main class="sign">
  <svg class="sign-panel" viewBox="0 0 884 793" aria-hidden="true">
    <defs>
      <radialGradient id="panel-glow" cx="0.5" cy="0" r="1.05">
        <stop offset="0" stop-color="var(--blue-light)"/>
        <stop offset="0.45" stop-color="var(--blue-mid)"/>
        <stop offset="1" stop-color="var(--blue-deep)"/>
      </radialGradient>
    </defs>
    <rect width="884" height="793" fill="var(--leaf-green)"/>
    <path d="M540 0 H884 V478 C840 660 720 793 540 793 H0 V318 C50 120 260 0 540 0 Z" fill="url(#panel-glow)"/>
  </svg>

  <div class="brand">
    <span class="brand-mark"></span>
    <h1 class="brand-name">
      <span class="line-main">Ridgeline</span>
      <span class="line-sub">Fitness Centre</span>
    </h1>
  </div>

  <p class="tagline">Your personal training<br>studio &amp; boutique<br>coaching gym</p>

  <p class="contact">
    <svg class="contact-icon" viewBox="0 0 36 58" aria-label="Phone">
      <rect x="15" y="0" width="5" height="10" rx="2" fill="var(--ink)"/>
      <rect x="2" y="8" width="32" height="48" rx="7" fill="var(--ink)"/>
      <rect x="8" y="15" width="20" height="18" rx="2" fill="var(--blue-mid)"/>
      <circle cx="18" cy="45" r="4" fill="var(--blue-mid)"/>
    </svg>
    <span class="contact-number">9471-2836</span>
  </p>
</main>
</body>
</html>
```